Stationery Design Project for Nimbora, Chicago

Nimbora, a street parking application which helps car drivers find a street parking spot by offering an ideal path along which to look for parking. This path is calculated by our algorithm based on data (e.g. historical data, baseball games schedule, etc.). Along this path the driver will find a spot and will also save 70% of the search time. Customer we target is reg. between 21 and 45 yo.

We envision something young, fresh, bright and original. Slightly abstract maybe. It should represent the idea and elements of finding street parking in the city, e.g. car(s), parking spot, people, city, etc. (just ideas!).

Logo is attached.

Requirement:
- Business Cards (2 Sided Full Color CMYK)
- Letterhead (1 Sided Full Color CMYK)
- Envelope (1 Sided Full Color CMYK)
- Sticker (1 Sided Full Color CMYK), round with a 2inch diameter.

Reason: We're starting to get more and more designs and need more time to look into all of them. Very exciting!! Thanks to everybody!

Hi all, we're in the process of selecting our favs. Though choices!!! Really good submissions. Will keep you posted and sorry for the delay.

Target Market(s)

Car drivers and owners between 21 and 45

Industry/Entity Type

Parking

Requirements
Must have
• Sticker should be round and include company URL nimbora.com and the new logo which we will attach soon.
Should not have
• Should not be too serious or boring.

```html
<!DOCTYPE html>
<html lang="en">
<head>
<meta charset="utf-8">
<title>Nimbora Business Card</title>
<link rel="stylesheet" href="https://fonts.googleapis.com/css2?family=Open+Sans:wght@400;600;700&display=swap">
<style>
  :root {
    --backdrop: #d9d9d9;
    --card: #ffffff;
    --ink: #1a1a1a;
    --brand-blue: #1a7dc4;
    --brand-navy: #1f3d98;
    --mark-blue: #1f56b8;
    --steel-light: #c8c8c8;
    --steel-dark: #8a8a8a;
    --photo-light: #b9bcc0;
    --photo-dark: #6f7378;
  }
  * { margin: 0; padding: 0; box-sizing: border-box; }
  html, body {
    width: 956px; height: 1200px; overflow: hidden;
    background: var(--backdrop);
    font-family: "Open Sans", Arial, sans-serif;
    color: var(--ink);
  }
  .canvas { position: relative; width: 956px; height: 1200px; }
  .card {
    position: absolute; left: 62px; width: 798px; height: 455px;
    background: var(--card); border-radius: 26px;
    box-shadow: 3px 4px 8px rgba(0,0,0,0.25);
    overflow: hidden;
  }
  .card--front { top: 100px; }
  .card--back { top: 648px; }
  .brand-dot {
    position: absolute; border-radius: 50%; background: var(--mark-blue);
  }
  .card--front .brand-dot { left: 80px; top: 44px; width: 154px; height: 154px; }
  .brand-name {
    position: absolute; font-weight: 700; color: var(--ink); letter-spacing: 1px;
  }
  .card--front .brand-name { left: 262px; top: 70px; font-size: 84px; line-height: 100px; }
  .contact {
    position: absolute; left: 0; width: 798px; top: 254px;
    text-align: center; font-size: 19px; line-height: 33px;
  }
  .contact b { font-weight: 700; }
  .band {
    position: absolute; left: 0; width: 684px; height: 53px;
    background: linear-gradient(90deg, var(--brand-blue) 0%, var(--brand-blue) 45%, var(--brand-navy) 100%);
    color: #fff; text-align: center; line-height: 53px;
  }
  .card--front .band { top: 370px; font-size: 23px; font-weight: 600; }
  .card--back .band { top: 371px; font-size: 25px; font-weight: 400; }
  .band .spaced { letter-spacing: 6px; }
  .steel-tab {
    position: absolute; left: 694px; width: 104px; height: 53px;
    background: linear-gradient(90deg, var(--steel-dark), var(--steel-light) 60%, var(--steel-dark));
  }
  .card--front .steel-tab { top: 370px; }
  .card--back .steel-tab { top: 371px; }
  .card--back .brand-dot { left: 94px; top: 62px; width: 170px; height: 170px; }
  .card--back .brand-name { left: 38px; top: 248px; width: 282px; text-align: center; font-size: 46px; line-height: 56px; }
  .street-photo {
    position: absolute; left: 346px; top: 55px; width: 418px; height: 263px;
    background: linear-gradient(135deg, var(--photo-light), var(--photo-dark) 55%, var(--photo-light));
  }
</style>
</head>
<body>
<div class="canvas">
  <section class="card card--front">
    <div class="brand-dot"></div>
    <div class="brand-name">Nimbora</div>
    <div class="contact">
      <div><b>t</b> : 123-456-7890 &nbsp;|&nbsp; <b>m</b> : 123-456-7890</div>
      <div><b>e</b> : name@website.com &nbsp;|&nbsp; <b>w</b> : www.website.com</div>
      <div>City Name, Street Name, State Name, Country Code</div>
    </div>
    <div class="band">Your Name - Designation</div>
    <div class="steel-tab"></div>
  </section>

  <section class="card card--back">
    <div class="brand-dot"></div>
    <div class="brand-name">Nimbora</div>
    <div class="street-photo" role="img" aria-label="Photo of cars parked in marked street parking bays seen from above"></div>
    <div class="band">www.<span class="spaced">WEBSITE</span>.com</div>
    <div class="steel-tab"></div>
  </section>
</div>
</body>
</html>
```